Design a single page Shopify store web page

We are looking to have a page designed for a single page Shopify store with 2 products. We already have a basic structure that we like, though we are open to suggestions. We are looking for somebody to provide a design/color scheme that we can then implement using Shopify's templating system. We can handle the implementation(HTML / CSS / jS) as we already have 2 web developers on the team, but have not been able to find a design we liked.

The job would consist of providing a mockup (photoshop or otherwise) and any vector graphics you choose to create for the site (we can provide product photos and other images).

You can also look at http://brickdune.com.au for some of our design direction we have used so far

Target Market(s)

Young Australian Males (18 - 49)

Industry/Entity Type

Store

Number of Pages Required

1 page

Font styles to use
Serif
Sans Serif

Requirements
Must have
• Single Page Design
• E-commerce Product Purchase
• Manly (whatever interpretation of that you have)

```html
<!DOCTYPE html>
<html lang="en">
<head>
<meta charset="utf-8">
<title>Brick Dune – Underwear Plans</title>
<link rel="stylesheet" href="https://fonts.googleapis.com/css2?family=Roboto:wght@300;400;500;700&display=swap">
<style>
:root{
  --navy:#0f2233;
  --slate:#3b4a57;
  --sky:#0aa0d6;
  --ink:#1e2a33;
  --paper:#f7f7f7;
  --coral:#e8604a;
  --coral-deep:#d9503b;
  --price:#e0452f;
  --green:#5cb85c;
  --faq:#7dd0ea;
  --grey-text:#7a7a7a;
  --dark-ring:#2b2b2b;
}
*{box-sizing:border-box;margin:0;padding:0}
html,body{width:1200px;height:2305px;overflow:hidden}
body{font-family:"Roboto",Arial,sans-serif;background:var(--paper);color:var(--ink);position:relative}
.abs{position:absolute}

/* header */
.site-header{position:absolute;left:0;top:0;width:1200px;height:101px;background:var(--navy)}
.brand{position:absolute;left:174px;top:28px;font-size:38px;font-weight:500;color:#cfe9f5;letter-spacing:1px;line-height:44px}
.main-nav{position:absolute;top:35px;left:513px;height:30px;font-size:14px;color:#fff}
.main-nav span{position:absolute;top:6px;white-space:nowrap}
.main-nav .signup{position:absolute;left:395px;top:0;width:118px;height:30px;border:1.5px solid #fff;border-radius:3px;display:flex;align-items:center;justify-content:center;font-size:14px}

/* hero */
.hero{position:absolute;left:0;top:101px;width:1200px;height:557px;background:var(--slate);overflow:hidden}
.hero-bg{position:absolute;left:0;top:0}
.hero-product{position:absolute;left:177px;top:114px;width:302px;height:300px;border-radius:14px 14px 30px 30px;background:linear-gradient(180deg,#6e6f86 0%,#7d7e96 60%,#6a6b80 100%)}
.hero-arrow{position:absolute}
.hero-copy{position:absolute;right:170px;top:130px;text-align:right;font-weight:500}
.hero-copy .lead{color:#fff;font-size:40px;line-height:45px}
.hero-copy .dark{color:var(--navy);font-size:29px;line-height:44px}
.hero-copy .light{color:#fff;font-size:29px;line-height:44px}

/* how it works */
.how{position:absolute;left:0;top:658px;width:1200px;height:471px;background:var(--paper)}
.section-title{position:absolute;left:0;width:1200px;text-align:center;font-weight:400;letter-spacing:2px}
.how .section-title{top:40px;font-size:34px;color:#222}
.step{position:absolute;top:0;width:260px;height:471px;text-align:center}
.step-title{position:absolute;top:314px;left:0;width:260px;font-size:20px;font-weight:500;color:#222;letter-spacing:.5px}
.step-text{position:absolute;top:354px;left:41px;width:178px;font-size:12px;line-height:20px;color:var(--grey-text);font-weight:300}

/* plans */
.plans{position:absolute;left:0;top:1129px;width:1200px;height:527px;background:linear-gradient(135deg,#ec6f58 0%,var(--coral) 50%,var(--coral-deep) 100%)}
.plans .section-title{top:18px;font-size:34px;color:#fff}
.plan-card{position:absolute;top:89px;width:404px;height:288px;background:#fff}
.plan-name{position:absolute;top:11px;left:0;width:100%;text-align:center;font-size:18px;letter-spacing:1.5px;color:#222}
.photo-main{position:absolute;left:15px;top:47px;width:207px;height:215px}
.photo-small{position:absolute;left:232px;width:153px;height:45px}
.price{position:absolute;left:232px;top:162px;width:153px;text-align:center;font-size:36px;color:var(--price)}
.buy{position:absolute;left:232px;top:219px;width:150px;height:43px;background:var(--green);color:#fff;font-size:20px;letter-spacing:1.5px;display:flex;align-items:center;justify-content:center}
.perk{position:absolute;top:406px;width:200px;height:46px;background:#fff;color:var(--coral);font-size:11px;letter-spacing:.6px;display:flex;align-items:center;justify-content:center}

/* faq */
.faq{position:absolute;left:0;top:1656px;width:1200px;height:520px;background:var(--paper)}
.faq .section-title{top:32px;font-size:34px;color:#222}
.faq-item{position:absolute;width:264px;height:112px;background:var(--faq);text-align:center;padding:22px 14px 0}
.faq-q{font-size:13px;font-weight:500;color:#1a2a36;letter-spacing:.3px}
.faq-a{margin-top:12px;font-size:12px;line-height:20px;color:#fff}

/* footer */
.site-footer{position:absolute;left:0;top:2176px;width:1200px;height:129px;background:var(--navy);color:#fff}
.footer-links{position:absolute;left:174px;top:38px;font-size:14px;letter-spacing:.3px}
.copyright{position:absolute;left:174px;top:71px;font-size:14px;letter-spacing:.3px}
.social{position:absolute;left:676px;top:43px;display:flex;gap:12px}
.social span{width:35px;height:35px;background:#3e6f9a;display:block}
.payment{position:absolute;left:882px;top:47px;display:flex;gap:8px}
.payment span{width:42px;height:27px;border-radius:3px;background:#9fb8cc;display:block}
</style>
</head>
<body>

<header class="site-header">
  <div class="brand">BRICK DUNE</div>
  <nav class="main-nav">
    <span style="left:0">HOW IT WORKS</span>
    <span style="left:146px">PLANS</span>
    <span style="left:234px">FAQ</span>
    <span style="left:301px">ABOUT US</span>
    <span class="signup">SIGN UP NOW</span>
  </nav>
</header>

<section class="hero">
  <svg class="hero-bg" width="1200" height="557" viewBox="0 0 1200 557">
    <polygon points="719,0 1200,0 1200,557 403,557" fill="#0aa0d6"/>
  </svg>
  <div class="hero-product" role="img" aria-label="Grey boxer brief product photo"></div>
  <svg class="hero-arrow" style="left:62px;top:245px" width="42" height="42" viewBox="0 0 42 42">
    <circle cx="21" cy="21" r="21" fill="#1c2630"/>
    <polyline points="24,13 16,21 24,29" fill="none" stroke="#9aa5ad" stroke-width="2"/>
  </svg>
  <svg class="hero-arrow" style="left:1098px;top:246px" width="42" height="42" viewBox="0 0 42 42">
    <circle cx="21" cy="21" r="21" fill="#7fd3f0"/>
    <polyline points="18,13 26,21 18,29" fill="none" stroke="#0a6f96" stroke-width="2"/>
  </svg>
  <div class="hero-copy">
    <div class="lead">AUTOMATE YOUR</div>
    <div class="lead">LIFE</div>
    <div class="dark">NEW UNDER WEAR AND</div>
    <div class="light">SCOCK</div>
    <div class="dark">DELIVERED TO YOUR DOOR</div>
    <div class="light">WENT YOU NEED IT</div>
  </div>
</section>

<section class="how">
  <h2 class="section-title">HOW IT WORKS</h2>
  <svg class="abs" style="left:0;top:0" width="1200" height="300" viewBox="0 0 1200 300">
    <g>
      <circle cx="298" cy="204" r="77" fill="var(--dark-ring)"/><circle cx="298" cy="204" r="46" fill="var(--sky)"/>
      <circle cx="595" cy="204" r="77" fill="var(--dark-ring)"/><circle cx="595" cy="204" r="46" fill="var(--sky)"/>
      <circle cx="891" cy="204" r="77" fill="var(--dark-ring)"/><circle cx="891" cy="204" r="46" fill="var(--sky)"/>
    </g>
    <g font-family="Roboto, sans-serif" font-size="40" font-weight="700" fill="#fff" text-anchor="middle">
      <text x="298" y="219">1</text><text x="595" y="219">2</text><text x="891" y="219">3</text>
    </g>
    <polyline points="427,169 452,204 427,239" fill="none" stroke="#555" stroke-width="1.5"/>
    <polyline points="726,169 751,204 726,239" fill="none" stroke="#555" stroke-width="1.5"/>
  </svg>
  <div class="step" style="left:168px">
    <div class="step-title">CHOOSE A PLAN</div>
    <div class="step-text">There will be plans for all bud-gets and styles.</div>
  </div>
  <div class="step" style="left:465px">
    <div class="step-title">CHOOSE HOW OFTEN</div>
    <div class="step-text">Decide whether you would like to receive new packages every 3 or 6 months.</div>
  </div>
  <div class="step" style="left:761px">
    <div class="step-title">GET YOUR PACK</div>
    <div class="step-text">We'll send out your first pack right away and then again every 3 or 6 months.</div>
  </div>
</section>

<section class="plans">
  <h2 class="section-title">PLAN</h2>
  <article class="plan-card" style="left:174px">
    <div class="plan-name">COMFORT</div>
    <div class="photo-main" role="img" aria-label="Model wearing white briefs" style="background:linear-gradient(160deg,#c9a58a,#e9ddd2 60%,#f3f1ee)"></div>
    <div class="photo-small" role="img" aria-label="Black briefs" style="top:47px;background:linear-gradient(180deg,#e8e8e8,#2a2a2a 50%,#e8e8e8)"></div>
    <div class="photo-small" role="img" aria-label="Red swim briefs by the sea" style="top:91px;background:linear-gradient(180deg,#7fa9b3,#8b2a35 55%,#9bc0c6)"></div>
    <div class="price">$30</div>
    <div class="buy">GET IT !</div>
  </article>
  <article class="plan-card" style="left:622px">
    <div class="plan-name">STYLE</div>
    <div class="photo-main" role="img" aria-label="Black trunks with printed waistband" style="background:linear-gradient(160deg,#1d1d1f,#3a3a3c 55%,#c49a7e)"></div>
    <div class="photo-small" role="img" aria-label="Black and grey briefs" style="top:47px;background:linear-gradient(90deg,#f0f0f0,#2b2b2b 40%,#8c8c8c 80%,#f0f0f0)"></div>
    <div class="photo-small" role="img" aria-label="White trunks on dark backdrop" style="top:91px;background:linear-gradient(180deg,#2a3440,#e8e8ee 60%,#2a3440)"></div>
    <div class="price">$30</div>
    <div class="buy">GET IT !</div>
  </article>
  <div class="perk" style="left:174px">FREE SHIPPING</div>
  <div class="perk" style="left:390px">EASY RETURES</div>
  <div class="perk" style="left:608px">CANCEL WHENEVER</div>
  <div class="perk" style="left:825px">SATISFATION GUARANTEED</div>
</section>

<section class="faq">
  <h2 class="section-title">FAQ</h2>
  <div class="faq-item" style="left:175px;top:105px"><div class="faq-q">WHAT IS BRICK DUNE?</div><div class="faq-a">Lorem Ipsum is simply dummy text of the printing and typesetting industry</div></div>
  <div class="faq-item" style="left:466px;top:105px"><div class="faq-q">WHAT ABOUT SIZING?</div><div class="faq-a">Lorem Ipsum is simply dummy text of the printing and typesetting industry</div></div>
  <div class="faq-item" style="left:759px;top:105px"><div class="faq-q">SHIPPING POLICY</div><div class="faq-a">Lorem Ipsum is simply dummy text of the printing and typesetting industry</div></div>
  <div class="faq-item" style="left:175px;top:234px"><div class="faq-q">HOW DOES PAYMENT WORK?</div><div class="faq-a">Lorem Ipsum is simply dummy text of the printing and typesetting industry</div></div>
  <div class="faq-item" style="left:466px;top:234px"><div class="faq-q">RETURNS POLICY</div><div class="faq-a">Lorem Ipsum is simply dummy text of the printing and typesetting industry</div></div>
  <div class="faq-item" style="left:759px;top:234px"><div class="faq-q">WHAT BRANDS DO YOU STOCK?</div><div class="faq-a">Lorem Ipsum is simply dummy text of the printing and typesetting industry</div></div>
  <div class="faq-item" style="left:175px;top:366px"><div class="faq-q">SHIPPING POLICY</div><div class="faq-a">Lorem Ipsum is simply dummy text of the printing and typesetting industry</div></div>
  <div class="faq-item" style="left:466px;top:366px"><div class="faq-q">WHAT IS BRICK DUNE?</div><div class="faq-a">Lorem Ipsum is simply dummy text of the printing and typesetting industry</div></div>
  <div class="faq-item" style="left:759px;top:366px"><div class="faq-q">HOW DOES PAYMENT WORK?</div><div class="faq-a">Lorem Ipsum is simply dummy text of the printing and typesetting industry</div></div>
</section>

<footer class="site-footer">
  <div class="footer-links">Shipping &nbsp;|&nbsp; Returns &nbsp;|&nbsp; payment &nbsp;|&nbsp; Terms &nbsp;|&nbsp; Privacy</div>
  <div class="copyright">© BRICK DUNE 2014</div>
  <div class="social" aria-label="Social links"><span></span><span></span><span></span><span></span></div>
  <div class="payment" aria-label="Accepted payment methods"><span></span><span></span><span></span></div>
</footer>

</body>
</html>
```